KLV Plant Services

We are a heavy diesel mechanical business with additional air con certificates, remapping engine rebuilt

Contact Information for Business Card

Company Name, Director Name, Managing Director, Contact details, email and website

Font styles to use
Serif
Script

```html
<!DOCTYPE html>
<html lang="en">
<head>
<meta charset="utf-8">
<title>KLV Plant Services – Business Card</title>
<link rel="stylesheet" href="https://fonts.googleapis.com/css2?family=Roboto:wght@400;500;700&display=swap">
<style>
  :root {
    --backdrop: #dcdcdc;
    --navy: #020361;
    --paper: #f4f4f5;
    --ink: #000000;
    --light: #ffffff;
    --faint-brand: #5a5fd0;
    --shadow: rgba(0, 0, 0, 0.28);
  }
  * { box-sizing: border-box; margin: 0; padding: 0; }
  html, body {
    width: 1200px; height: 1040px; overflow: hidden;
    background: var(--backdrop);
    font-family: "Roboto", Arial, sans-serif;
  }
  .stage { position: relative; width: 1200px; height: 1040px; }
  .card {
    position: absolute; left: 280px; width: 640px; height: 366px;
    border-radius: 16px; overflow: hidden;
    box-shadow: 0 3px 5px var(--shadow);
  }
  .card--front { top: 120px; background: var(--paper); }
  .card--back { top: 560px; background: var(--navy); }
  .card__bands { position: absolute; inset: 0; width: 640px; height: 366px; }
  .band--navy { fill: var(--navy); }
  .band--ink { fill: var(--ink); }

  .brand {
    position: absolute; left: 68px; top: 126px;
    display: flex; align-items: center; gap: 10px;
  }
  .brand__name {
    font-weight: 700; font-size: 23px; color: var(--navy); white-space: nowrap;
  }
  .brand__dot {
    width: 18px; height: 18px; border-radius: 50%; background: var(--navy);
  }

  .contact {
    position: absolute; right: 39px; top: 74px;
    text-align: right; color: var(--light);
  }
  .contact__name { font-weight: 700; font-size: 24px; line-height: 1.2; }
  .contact__role { font-size: 15px; line-height: 1.2; }
  .contact__address { margin-top: 54px; font-size: 16px; line-height: 20px; }
  .contact__lines { margin-top: 14px; font-size: 16px; line-height: 20px; list-style: none; }
  .contact__lines li { display: flex; justify-content: flex-end; align-items: center; gap: 8px; }
  .contact__lines svg { width: 13px; height: 13px; fill: var(--light); }

  .back-brand {
    position: absolute; left: 0; right: 0; top: 172px; text-align: center;
    font-weight: 700; font-size: 38px; color: var(--faint-brand);
  }
  .back-web {
    position: absolute; left: 0; right: 0; top: 324px; text-align: center;
    color: var(--light); font-size: 15px; letter-spacing: 3.5px;
  }
</style>
</head>
<body>
<main class="stage">
  <section class="card card--front">
    <svg class="card__bands" viewBox="0 0 640 366" aria-hidden="true">
      <polygon class="band--ink" points="462,0 468,0 178,366 166,366"/>
      <polygon class="band--navy" points="471,0 640,0 640,366 213,366"/>
    </svg>
    <div class="brand">
      <span class="brand__name">KLV Plant Services</span>
      <span class="brand__dot"></span>
    </div>
    <div class="contact">
      <p class="contact__name">Owen Hartley</p>
      <p class="contact__role">Managing Director</p>
      <p class="contact__address">2719 Harbor Lane<br>Maple Ridge, NY 10592</p>
      <ul class="contact__lines">
        <li>(555) 0142-7788
          <svg viewBox="0 0 24 24" aria-hidden="true"><path d="M6.6 10.8a15.1 15.1 0 0 0 6.6 6.6l2.2-2.2c.3-.3.7-.4 1-.2 1.1.4 2.3.6 3.6.6.6 0 1 .4 1 1V20c0 .6-.4 1-1 1A17 17 0 0 1 3 4c0-.6.4-1 1-1h3.5c.6 0 1 .4 1 1 0 1.3.2 2.5.6 3.6.1.3 0 .7-.2 1z"/></svg>
        </li>
        <li>name@KLV.com
          <svg viewBox="0 0 24 24" aria-hidden="true"><path d="M2 5h20v14H2z M2 5l10 8 10-8" fill="none" stroke="#fff" stroke-width="0"/><path d="M2 6v12h20V6l-10 7z M3 5l9 6.5L21 5z"/></svg>
        </li>
        <li>www.KLV.com
          <svg viewBox="0 0 24 24" aria-hidden="true"><circle cx="12" cy="12" r="10"/><path d="M8 6c2 1 3 3 2 5s-3 2-3 5M15 4c-1 2 1 3 3 4M16 14c-2 0-3 2-2 5" stroke="var(--navy)" stroke-width="2" fill="none"/></svg>
        </li>
      </ul>
    </div>
  </section>

  <section class="card card--back">
    <p class="back-brand">KLV Plant Services</p>
    <p class="back-web">www.KLV.com</p>
  </section>
</main>
</body>
</html>
```